Letterhead, stationery and email signature for construction business

I need the letterhead, stationery and email signature designs for a construction business. I want them to have a corporate feel to them.

I've attached the logo for reference.

```html
<!DOCTYPE html>
<html lang="en">
<head>
<meta charset="utf-8">
<title>Harlow Build – Stationery</title>
<link rel="stylesheet" href="https://fonts.googleapis.com/css2?family=Open+Sans:wght@400;600;700&display=swap">
<style>
  :root {
    --brand-blue: #375a98;
    --brand-grey: #5b5e66;
    --ink: #55585e;
    --paper: #f7f7f7;
    --backdrop: #e6e6e8;
    --signature: #2a3550;
  }
  * { box-sizing: border-box; margin: 0; padding: 0; }
  html, body { width: 1200px; height: 795px; overflow: hidden; }
  body {
    background: var(--backdrop);
    font-family: "Open Sans", Arial, sans-serif;
    color: var(--ink);
    position: relative;
  }

  /* Letterhead */
  .letterhead {
    position: absolute; left: 90px; top: 45px;
    width: 500px; height: 705px;
    background: var(--paper);
    box-shadow: 0 2px 10px rgba(0,0,0,0.12);
    overflow: hidden;
  }
  .brand {
    display: flex; align-items: center; gap: 8px;
    font-weight: 700; color: var(--brand-blue);
    letter-spacing: 0.04em; line-height: 1;
  }
  .brand-square { width: 20px; height: 20px; background: var(--brand-blue); }
  .letterhead .brand { position: absolute; left: 48px; top: 46px; font-size: 19px; }

  .contact {
    position: absolute; right: 40px; top: 100px;
    border-left: 1px solid #c9cacd; padding-left: 12px;
    font-size: 8.5px; font-weight: 600; line-height: 1.55; color: #3f4248;
  }
  .contact-row { display: flex; align-items: center; gap: 5px; }
  .contact-row svg { width: 8px; height: 8px; fill: var(--brand-blue); flex: none; }

  .letter-body {
    position: absolute; left: 48px; top: 175px; width: 400px;
    font-size: 8.6px; line-height: 1.6;
  }
  .salutation { margin-bottom: 10px; }
  .letter-body p { margin-bottom: 10px; }
  .closing { margin-top: 6px; }
  .signature {
    display: block; width: 70px; height: 34px; margin-top: 10px;
    background: linear-gradient(90deg, rgba(42,53,80,0.18), rgba(42,53,80,0.05));
    border-radius: 3px;
  }

  .footer-band {
    position: absolute; left: 0; bottom: 0; width: 100%; height: 9px;
    background: var(--brand-blue);
  }
  .footer-band::before {
    content: ""; position: absolute; left: 0; top: 0;
    width: 26px; height: 100%; background: var(--brand-grey);
  }

  /* Envelope */
  .envelope {
    position: absolute; left: 630px; top: 250px;
    width: 520px; height: 262px;
    background: var(--paper);
    box-shadow: 0 2px 10px rgba(0,0,0,0.12);
  }
  .envelope-flap {
    position: absolute; left: 0; top: 0; width: 100%; height: 118px;
    background: var(--brand-blue);
    border-radius: 0 0 16px 16px;
    display: flex; align-items: center; justify-content: center;
  }
  .envelope .brand { color: #ffffff; font-size: 26px; }
  .envelope .brand-square { width: 28px; height: 28px; background: #ffffff; }
</style>
</head>
<body>

<article class="letterhead">
  <div class="brand"><span class="brand-square"></span>HARLOW BUILD</div>

  <address class="contact">
    <div>4470 Maple Ridge Road.</div>
    <div>Fairview, CA 90210</div>
    <div class="contact-row">
      <svg viewBox="0 0 10 10"><path d="M2 0.5 L4 2.5 L3 4 Q4.5 6 6 7 L7.5 6 L9.5 8 L8 9.5 Q3 9 0.5 2 Z"/></svg>(555)012-0188
    </div>
    <div class="contact-row">
      <svg viewBox="0 0 10 10"><path d="M0 2 H10 V8.5 H0 Z M0.8 2.6 L5 5.6 L9.2 2.6 V3.4 L5 6.4 L0.8 3.4 Z" fill-rule="evenodd"/></svg>info@harlowbuild.com
    </div>
    <div class="contact-row">
      <svg viewBox="0 0 10 10"><circle cx="5" cy="5" r="4.5"/></svg>www.harlowbuild.com
    </div>
  </address>

  <div class="letter-body">
    <div class="salutation">Dear customer,</div>
    <p>Lorem ipsum dolor sit amet, consectetur adipisicing elit, sed do eiusmod tempor incididunt ut labore et dolore magna aliqua. Ut enim ad minim veniam, quis nostrud exercitation ullamco laboris nisi ut aliquip ex ea commodo consequat. Duis aute irure dolor in reprehenderit in voluptate velit esse cillum dolore eu fugiat nulla pariatur. Excepteur sint occaecat cupidatat non proident, sunt in culpa qui officia deserunt mollit anim id est laborum.</p>
    <p>Lorem ipsum dolor sit amet, consectetur adipisicing elit, sed do eiusmod tempor incididunt ut labore et dolore magna aliqua. Ut enim ad minim veniam, quis nostrud exercitation ullamco laboris nisi ut aliquip ex ea commodo consequat. Duis aute irure dolor in reprehenderit in voluptate velit esse cillum dolore eu fugiat nulla pariatur. Excepteur sint occaecat cupidatat non proident, sunt in culpa qui officia deserunt mollit anim id est laborum.</p>
    <p>Lorem ipsum dolor sit amet, consectetur adipisicing elit, sed do eiusmod tempor incididunt ut labore et dolore magna aliqua. Ut enim ad minim veniam, quis nostrud exercitation ullamco laboris nisi ut aliquip ex ea commodo consequat. Duis aute irure dolor in reprehenderit in voluptate velit esse cillum dolore eu fugiat nulla pariatur. Excepteur sint occaecat cupidatat non proident, sunt in culpa qui officia deserunt mollit anim id est laborum.</p>
    <p>Lorem ipsum dolor sit amet, consectetur adipisicing elit, sed do eiusmod tempor incididunt ut labore et dolore magna aliqua. Ut enim ad minim veniam, quis nostrud exercitation ullamco laboris nisi ut aliquip ex ea commodo consequat. Duis aute irure dolor.</p>
    <div class="closing">Yours Sincerely,</div>
    <span class="signature" role="img" aria-label="Handwritten signature"></span>
  </div>

  <div class="footer-band"></div>
</article>

<article class="envelope">
  <div class="envelope-flap">
    <div class="brand"><span class="brand-square"></span>HARLOW BUILD</div>
  </div>
</article>

</body>
</html>
```